I need a complete stationary pack for a real estate office that sells and manages residential proper

We need a stationary design pack for my real estate office called ‘brightkeyhomes’ that is in Queensland Australia. My offices are both in suburban and coastal locations in the south west corner of Queensland at the Coral Bay Shore and Brisbane.
We predominately manage real estate on behalf of owners and sell property in the residential sector.
I have attached a copy of our existing design of my business card and do like the current concept/layout. In saying this you may be able to use this existing theme across to the other items required or see opportunity on how to improve what I have already.
I would like to see concepts for the following products:
- Letterhead
- Fax header
- Business cards
- Email signature
- With complements slips and
- Envelopes
I have attached our current logo that was designed by Artfolder and the font is Prelo.

I am looking for a contemporary design that is professional and reflects trust and professionalism. I am currently using the logo with a black background on some material as per the following link

http://www.plotlisting.com.au/property/for-sale/house/qld/merridale/?adid=4827305118&sp=7

I have posted another job 517362 for signage and the company car signage done too if you are interested.

Please do not hesitate to contact me should you have any questions. Thank you.

Target Market(s)

Western speaking people aged from 25 to 60 from modest backgrounds to well off individuals

Industry/Entity Type

Real Estate

Requirements
Must have
• Professional in appearance, show a mature and trustworthy image
Should not have
• As there is good colour with the logo, i am do not want over the top designs or colours

```html
<!DOCTYPE html>
<html lang="en">
<head>
<meta charset="utf-8">
<title>brightkeyhomes stationery pack</title>
<link href="https://fonts.googleapis.com/css2?family=Open+Sans:ital,wght@0,400;0,600;0,700;1,400&display=swap" rel="stylesheet">
<style>
:root{
  --bg:#e8e5e0;
  --paper:#ffffff;
  --navy:#2e3a50;
  --deep:#1d2a40;
  --ink:#3c4456;
  --muted:#6b7180;
  --rule:#9aa0aa;
  --red:#d8262c;
  --purple:#6b2d8d;
  --blue:#1f6fb8;
  --green:#2f9e46;
  --orange:#f08a1c;
  --yellow:#f2c31d;
  --flap-green:#2e9b4a;
  --flap-blue:#1c74bd;
  --flap-red:#d52a2f;
  --accent-text:#1f6fb8;
}
*{box-sizing:border-box;margin:0;padding:0}
html,body{width:1200px;height:900px;overflow:hidden}
body{background:var(--bg);font-family:"Open Sans",Arial,sans-serif;color:var(--ink);position:relative}
.sheet{position:absolute;background:var(--paper);overflow:hidden;box-shadow:0 1px 3px rgba(0,0,0,.18)}
.brand-bar{position:absolute;left:0;right:0;bottom:0;display:flex;flex-direction:column}
.brand-bar .colors{display:flex;height:3px}
.brand-bar .colors span{flex:1}
.brand-bar .base{background:var(--navy)}
.c-red{background:var(--red)}.c-purple{background:var(--purple)}.c-blue{background:var(--blue)}
.c-green{background:var(--green)}.c-orange{background:var(--orange)}.c-yellow{background:var(--yellow)}

.brand{display:flex;align-items:center;gap:5px;font-weight:600;color:var(--navy);letter-spacing:-.02em;white-space:nowrap}
.brand .dot{border-radius:50%;background:var(--orange);flex:none}
.brand.light{color:#fff}

.icon{display:inline-block;vertical-align:middle;margin-right:3px}
.contact-line{white-space:nowrap}

/* letterhead */
.letterhead{left:18px;top:15px;width:274px;height:418px}
.letterhead .brand{position:absolute;left:30px;top:92px;font-size:14px}
.letterhead .brand .dot{width:12px;height:12px}
.letterhead .head-contact{position:absolute;left:170px;top:70px;border-left:1px solid var(--rule);padding-left:6px;font-size:5.2px;line-height:7.6px}
.letterhead .body{position:absolute;left:27px;top:131px;width:246px;font-size:5.2px;line-height:6.5px;text-align:justify}
.letterhead .body p{margin-bottom:6px}
.letterhead .date,.letterhead .greet{font-size:6px;margin-bottom:4px;text-align:left}
.letterhead .sign{font-size:7px;margin-top:10px}
.letterhead .role{font-size:4.6px;color:var(--muted)}
.letterhead .brand-bar .base{height:7px}

/* folder */
.folder{left:305px;top:15px;width:297px;height:418px}
.folder .front{position:absolute;left:0;top:0;right:0;height:189px;display:flex;align-items:center;justify-content:center}
.folder .front .brand{font-size:19px}
.folder .front .brand .dot{width:16px;height:16px}
.folder .mid-bar{position:absolute;left:0;right:0;top:189px;display:flex;height:4px}
.folder .mid-bar span{flex:1}
.folder .back{position:absolute;left:0;right:0;top:193px;bottom:0;background:radial-gradient(ellipse at 45% 45%,#34435d 0%,var(--deep) 70%)}
.folder .back .web{position:absolute;bottom:12px;width:100%;text-align:center;font-size:5.5px;color:#c9cfda}

/* fax */
.fax{top:48px;width:273px;height:385px}
.fax-a{left:613px}.fax-b{left:899px}
.fax .brand{position:absolute;left:18px;top:48px;font-size:11px}
.fax .brand .dot{width:10px;height:10px}
.fax .head-contact{position:absolute;left:192px;top:28px;font-size:4.4px;line-height:5.8px}
.fax .title{position:absolute;right:15px;top:78px;font-size:10px;font-weight:700;color:var(--ink)}
.fax table.fields{position:absolute;left:18px;top:94px;width:240px;border-collapse:collapse;font-size:5px}
.fax table.fields td{border:1px solid #8c919b;height:11px;padding:0 3px}
.fax table.fields td.label{background:#eceef1;width:46px}
.fax .status{position:absolute;left:18px;top:160px;width:240px;display:flex;border:1px solid #8c919b;background:#eceef1;font-size:4.8px}
.fax .status span{flex:1;text-align:center;padding:2px 0;border-left:1px solid #8c919b}
.fax .status span:first-child{border-left:none}
.fax .comments{position:absolute;left:18px;top:171px;width:240px;height:167px;border:1px solid #8c919b;font-size:4.8px;text-align:center;padding-top:10px}
.fax .checks{position:absolute;left:18px;top:146px;width:245px;display:flex;justify-content:space-between;font-size:5px}
.fax .checks span{display:flex;align-items:center;gap:3px}
.fax .checks i{width:6px;height:6px;border:1px solid #7c818b;display:inline-block}
.fax .brand-bar .base{height:7px}

/* business cards */
.card-front{left:33px;top:452px;width:233px;height:130px}
.card-front .brand{position:absolute;left:16px;top:74px;font-size:11px}
.card-front .brand .dot{width:10px;height:10px}
.card-front .divider{position:absolute;left:123px;top:28px;width:1px;height:58px;background:var(--rule)}
.photo{background:linear-gradient(160deg,#b9c3cf,#5c6a7e);border:1px solid #fff}
.card-front .photo{position:absolute;left:134px;top:26px;width:32px;height:38px}
.card-front .name{position:absolute;left:172px;top:28px;font-size:7px;font-weight:700;color:var(--red)}
.card-front .role{position:absolute;left:172px;top:37px;font-size:4.6px;color:var(--green)}
.card-front .mob{position:absolute;left:172px;top:44px;font-size:5px}
.card-front .details{position:absolute;left:134px;top:68px;font-size:4.8px;line-height:6.4px}
.card-front .brand-bar .base{height:5px}

.card-back{left:33px;top:598px;width:231px;height:130px;background:radial-gradient(ellipse at 50% 40%,#34435d 0%,var(--deep) 75%)}
.card-back .brand{position:absolute;left:0;right:0;top:50px;justify-content:center;font-size:12px}
.card-back .brand .dot{width:11px;height:11px}
.card-back .web{position:absolute;bottom:8px;width:100%;text-align:center;font-size:4.6px;color:#c9cfda}

/* compliments slip */
.slip{left:278px;top:498px;width:356px;height:168px}
.slip .brand{position:absolute;left:20px;top:58px;font-size:12px}
.slip .brand .dot{width:11px;height:11px}
.slip .tag{position:absolute;right:18px;top:36px;font-size:9.5px;font-style:italic;color:var(--ink)}
.slip .foot{position:absolute;left:20px;top:127px;display:flex;font-size:5.6px;line-height:7.4px}
.slip .foot div{padding:0 6px;border-left:1px solid var(--rule)}
.slip .foot div:first-child{padding-left:0;border-left:none}
.slip .brand-bar .colors{height:3px}
.slip .brand-bar .base{height:9px}

/* envelopes */
.envelope{position:absolute;background:var(--paper);box-shadow:0 1px 3px rgba(0,0,0,.2);overflow:hidden}
.envelope svg.flap{position:absolute;left:0;top:0}
.envelope .mark{position:absolute;top:17px;width:20px;height:20px;border-radius:50%;background:#fff;left:50%;margin-left:-10px}
.env-green{left:648px;top:448px;width:473px;height:190px}
.env-blue{left:670px;top:512px;width:450px;height:190px}
.env-red{left:697px;top:577px;width:420px;height:190px}
.env-front{left:730px;top:658px;width:451px;height:195px}
.env-front .brand{position:absolute;left:26px;top:58px;font-size:13px}
.env-front .brand .dot{width:12px;height:12px}
.env-front .address{position:absolute;left:135px;top:36px;border-left:1px solid var(--rule);padding-left:8px;font-size:6.4px;line-height:8.6px}
.env-front .brand-bar .colors{height:4px}
.env-front .brand-bar .base{height:12px}

/* email signature */
.signature{left:33px;top:742px;width:534px;height:132px}
.signature .brand{position:absolute;left:46px;top:54px;font-size:19px}
.signature .brand .dot{width:17px;height:17px}
.signature .photo{position:absolute;left:290px;top:19px;width:40px;height:48px}
.signature .name{position:absolute;left:340px;top:30px;font-size:10px;font-weight:700;color:var(--red)}
.signature .role{position:absolute;left:340px;top:43px;font-size:8px;color:var(--green)}
.signature .mob{position:absolute;left:340px;top:54px;font-size:9px}
.signature .rule{position:absolute;left:290px;top:72px;width:242px;height:1px;background:var(--rule)}
.signature .details{position:absolute;left:290px;top:76px;font-size:8.4px;line-height:11px}
.web-link{color:var(--accent-text)}
</style>
</head>
<body>

<!-- Letterhead -->
<section class="sheet letterhead" aria-label="Letterhead">
  <div class="brand"><span class="dot"></span>brightkeyhomes</div>
  <div class="head-contact">
    <div class="contact-line">Shop 4, 52 Harbour Parade,</div>
    <div class="contact-line">Kelso QLD 4560</div>
    <div class="contact-line"><svg class="icon" width="4" height="5" viewBox="0 0 4 5"><rect x=".5" y=".2" width="3" height="4.6" rx=".6" fill="var(--red)"/></svg>0412 558 207</div>
    <div class="contact-line"><svg class="icon" width="4" height="5" viewBox="0 0 4 5"><rect x=".5" y=".2" width="3" height="4.6" rx=".6" fill="var(--red)"/></svg>07 5491 2260</div>
    <div class="contact-line"><svg class="icon" width="5" height="4" viewBox="0 0 5 4"><rect x=".2" y=".4" width="4.6" height="3.2" fill="var(--red)"/></svg>daniel@brightkeyhomes.com.au</div>
    <div class="contact-line web-link"><svg class="icon" width="4" height="4" viewBox="0 0 4 4"><circle cx="2" cy="2" r="1.8" fill="var(--red)"/></svg>www.brightkeyhomes.com.au</div>
  </div>
  <div class="body">
    <div class="date">Jan/01/2015</div>
    <div class="greet">Dear Sarah,</div>
    <p>Thank you for choosing our office to look after your home. We have reviewed the details you sent and prepared a short summary of the next steps. Our team will contact you this week to arrange an inspection and agree on a suitable time for photos, signage and the first open home.</p>
    <p>During the campaign we will keep you informed of every enquiry, offer and buyer comment. Weekly reports will show how the market is responding, and we will suggest changes to price or marketing whenever the feedback supports it. Our aim is a clear, calm process with no surprises along the way.</p>
    <p>If you have any questions before then, please call the office or reply to this letter. We look forward to working with you and helping you reach a great result for your property.</p>
    <div class="sign">Peter Lane</div>
    <div class="role">Company Director</div>
  </div>
  <div class="brand-bar"><div class="colors"><span class="c-red"></span><span class="c-purple"></span><span class="c-blue"></span><span class="c-green"></span><span class="c-orange"></span><span class="c-yellow"></span></div><div class="base"></div></div>
</section>

<!-- Presentation folder -->
<section class="sheet folder" aria-label="Presentation folder">
  <div class="front"><div class="brand"><span class="dot"></span>brightkeyhomes</div></div>
  <div class="mid-bar"><span class="c-red"></span><span class="c-purple"></span><span class="c-blue"></span><span class="c-green"></span><span class="c-orange"></span><span class="c-yellow"></span></div>
  <div class="back"><div class="web">www.brightkeyhomes.com.au</div></div>
</section>

<!-- Fax header A -->
<section class="sheet fax fax-a" aria-label="Fax header">
  <div class="brand"><span class="dot"></span>brightkeyhomes</div>
  <div class="head-contact">
    <div>Shop 4, 52 Harbour Parade,</div><div>Kelso QLD 4560</div>
    <div>07 5491 2260</div><div>daniel@brightkeyhomes.com.au</div><div class="web-link">www.brightkeyhomes.com.au</div>
  </div>
  <div class="title">FAX</div>
  <table class="fields">
    <tr><td class="label">To:</td><td></td><td class="label">From:</td><td></td></tr>
    <tr><td class="label">Fax:</td><td></td><td class="label">Pages:</td><td></td></tr>
    <tr><td class="label">Phone:</td><td></td><td class="label">Date:</td><td></td></tr>
    <tr><td class="label">Re:</td><td></td><td class="label">CC:</td><td></td></tr>
  </table>
  <div class="status"><span>Urgent</span><span>For Review</span><span>Please comment</span><span>Please Reply</span><span>Please Recycle</span></div>
  <div class="comments">COMMENTS</div>
  <div class="brand-bar"><div class="colors"><span class="c-red"></span><span class="c-purple"></span><span class="c-blue"></span><span class="c-green"></span><span class="c-orange"></span><span class="c-yellow"></span></div><div class="base"></div></div>
</section>

<!-- Fax header B -->
<section class="sheet fax fax-b" aria-label="Fax header, checkbox version">
  <div class="brand"><span class="dot"></span>brightkeyhomes</div>
  <div class="head-contact">
    <div>Shop 4, 52 Harbour Parade,</div><div>Kelso QLD 4560</div>
    <div>07 5491 2260</div><div>daniel@brightkeyhomes.com.au</div><div class="web-link">www.brightkeyhomes.com.au</div>
  </div>
  <div class="title">FAX</div>
  <table class="fields">
    <tr><td class="label">To:</td><td></td><td class="label">From:</td><td></td></tr>
    <tr><td class="label">Fax:</td><td></td><td class="label">Pages:</td><td></td></tr>
    <tr><td class="label">Phone:</td><td></td><td class="label">Date:</td><td></td></tr>
    <tr><td class="label">Re:</td><td></td><td class="label">CC:</td><td></td></tr>
  </table>
  <div class="checks"><span><i></i>Urgent</span><span><i></i>For Review</span><span><i></i>Please comment</span><span><i></i>Please Reply</span><span><i></i>Please Recycle</span></div>
  <div class="brand-bar"><div class="colors"><span class="c-red"></span><span class="c-purple"></span><span class="c-blue"></span><span class="c-green"></span><span class="c-orange"></span><span class="c-yellow"></span></div><div class="base"></div></div>
</section>

<!-- Business card front -->
<section class="sheet card-front" aria-label="Business card front">
  <div class="brand"><span class="dot"></span>brightkeyhomes</div>
  <div class="divider"></div>
  <div class="photo" role="img" aria-label="Portrait photo of the principal"></div>
  <div class="name">Daniel Marsh</div>
  <div class="role">Principal</div>
  <div class="mob"><svg class="icon" width="4" height="5" viewBox="0 0 4 5"><rect x=".5" y=".2" width="3" height="4.6" rx=".6" fill="var(--red)"/></svg>0412 558 207</div>
  <div class="details">
    <div>Shop 4, 52 Harbour Parade,</div>
    <div>Kelso QLD 4560</div>
    <div><svg class="icon" width="5" height="4" viewBox="0 0 5 4"><path d="M.3 3.6 1.2 1 Q2.5 .2 3.8 1 L4.7 3.6Z" fill="var(--red)"/></svg>07 5491 2260</div>
    <div><svg class="icon" width="5" height="4" viewBox="0 0 5 4"><rect x=".2" y=".4" width="4.6" height="3.2" fill="var(--red)"/></svg>daniel@brightkeyhomes.com.au</div>
    <div class="web-link"><svg class="icon" width="4" height="4" viewBox="0 0 4 4"><circle cx="2" cy="2" r="1.8" fill="var(--red)"/></svg>www.brightkeyhomes.com.au</div>
  </div>
  <div class="brand-bar"><div class="colors"><span class="c-red"></span><span class="c-purple"></span><span class="c-blue"></span><span class="c-green"></span><span class="c-orange"></span><span class="c-yellow"></span></div><div class="base"></div></div>
</section>

<!-- Business card back -->
<section class="sheet card-back" aria-label="Business card back">
  <div class="brand light"><span class="dot"></span>brightkeyhomes</div>
  <div class="web">www.brightkeyhomes.com.au</div>
</section>

<!-- With compliments slip -->
<section class="sheet slip" aria-label="With compliments slip">
  <div class="brand"><span class="dot"></span>brightkeyhomes</div>
  <div class="tag">With Compliments</div>
  <div class="foot">
    <div>Shop 4, 52 Harbour Parade,<br>Kelso QLD 4560</div>
    <div>0412 558 207<br>07 5491 2260</div>
    <div>daniel@brightkeyhomes.com.au<br>www.brightkeyhomes.com.au</div>
  </div>
  <div class="brand-bar"><div class="colors"><span class="c-red"></span><span class="c-purple"></span><span class="c-blue"></span><span class="c-green"></span><span class="c-orange"></span><span class="c-yellow"></span></div><div class="base"></div></div>
</section>

<!-- Envelope backs -->
<section class="envelope env-green" aria-label="Envelope back, green flap">
  <svg class="flap" width="473" height="72" viewBox="0 0 473 72"><path d="M0 0H473V16C400 30 300 50 250 64Q236 70 222 64C170 50 70 30 0 16Z" fill="var(--flap-green)"/></svg>
  <div class="mark"></div>
</section>
<section class="envelope env-blue" aria-label="Envelope back, blue flap">
  <svg class="flap" width="450" height="72" viewBox="0 0 450 72"><path d="M0 0H450V16C380 30 290 50 240 64Q225 70 210 64C160 50 70 30 0 16Z" fill="var(--flap-blue)"/></svg>
  <div class="mark"></div>
</section>
<section class="envelope env-red" aria-label="Envelope back, red flap">
  <svg class="flap" width="420" height="72" viewBox="0 0 420 72"><path d="M0 0H420V16C360 30 270 50 224 64Q210 70 196 64C150 50 60 30 0 16Z" fill="var(--flap-red)"/></svg>
  <div class="mark"></div>
</section>

<!-- Envelope front -->
<section class="envelope env-front" aria-label="Envelope front">
  <div class="brand"><span class="dot"></span>brightkeyhomes</div>
  <div class="address">
    <div><svg class="icon" width="5" height="6" viewBox="0 0 5 6"><path d="M2.5 6C1 4 .2 3 .2 2.2A2.3 2.3 0 0 1 4.8 2.2C4.8 3 4 4 2.5 6Z" fill="var(--red)"/></svg>Shop 4, 52 Harbour Parade,</div>
    <div style="padding-left:8px">Kelso QLD 4560</div>
    <div class="web-link"><svg class="icon" width="5" height="5" viewBox="0 0 5 5"><circle cx="2.5" cy="2.5" r="2.3" fill="var(--red)"/></svg>www.brightkeyhomes.com.au</div>
  </div>
  <div class="brand-bar"><div class="colors"><span class="c-red"></span><span class="c-purple"></span><span class="c-blue"></span><span class="c-green"></span><span class="c-orange"></span><span class="c-yellow"></span></div><div class="base"></div></div>
</section>

<!-- Email signature -->
<section class="sheet signature" aria-label="Email signature">
  <div class="brand"><span class="dot"></span>brightkeyhomes</div>
  <div class="photo" role="img" aria-label="Portrait photo of the principal"></div>
  <div class="name">Daniel Marsh</div>
  <div class="role">Principal</div>
  <div class="mob"><svg class="icon" width="6" height="9" viewBox="0 0 6 9"><rect x=".6" y=".5" width="4.8" height="8" rx="1" fill="none" stroke="var(--red)" stroke-width="1"/></svg>0412 558 207</div>
  <div class="rule"></div>
  <div class="details">
    <div>Shop 4, 52 Harbour Parade, Kelso QLD 4560</div>
    <div><svg class="icon" width="9" height="7" viewBox="0 0 9 7"><path d="M.5 6.5 2 2Q4.5 .2 7 2L8.5 6.5Z" fill="var(--red)"/></svg>07 5491 2260</div>
    <div><svg class="icon" width="9" height="7" viewBox="0 0 9 7"><rect x=".5" y=".8" width="8" height="5.6" fill="var(--red)"/><path d="M.8 1.2 4.5 4 8.2 1.2" fill="none" stroke="#fff" stroke-width=".8"/></svg>daniel@brightkeyhomes.com.au</div>
    <div class="web-link"><svg class="icon" width="8" height="8" viewBox="0 0 8 8"><circle cx="4" cy="4" r="3.6" fill="var(--red)"/></svg>www.brightkeyhomes.com.au</div>
  </div>
</section>

</body>
</html>
```